I work in creative/artistic projects across different mediums.
It needs to communicate creativity, style, sexy, uniqueness, individuality and sophistication.
It should not look corporate.
Colours I like are black silver gold deep purple, chocolate, orchid.
It doesn't have to make use of all these colours.
I do not like bright primary colors.
Updates

Project Deadline Extended
Reason: Still in the communication process and to allow the person enough time to finish the design. Though i should know in the next day or two. Thank you.

Target Market(s)

creatives and companies wanting to inject creativity into thier business.

Industry/Entity Type

Work

Contact Information for Business Card

Corwin Haldley
0418592036
corwin@corwinhaldley-example.com

quietgoldenhourstudio.example.au

Requirements
Should not have
• Anything corporate OR OLD FASHIONED

```html
<!DOCTYPE html>
<html lang="en">
<head>
<meta charset="utf-8">
<title>Corwin Haldley — Business Card</title>
<link rel="stylesheet" href="https://fonts.googleapis.com/css2?family=Advent+Pro:wght@200;300&display=swap">
<style>
  :root {
    --panel-top: #3d3d3d;
    --panel-top-core: #2c2c2c;
    --panel-bottom: #2d2b2a;
    --ink: #ffffff;
  }
  * { margin: 0; padding: 0; box-sizing: border-box; }
  html, body {
    width: 742px;
    height: 1200px;
    overflow: hidden;
    background: var(--panel-bottom);
  }
  .card {
    position: relative;
    width: 742px;
    height: 1200px;
    font-family: "Advent Pro", sans-serif;
    color: var(--ink);
  }
  .card__brand-panel {
    position: absolute;
    left: 0; top: 0;
    width: 742px;
    height: 598px;
    background: radial-gradient(ellipse 62% 58% at 50% 42%, var(--panel-top-core) 0%, #333333 55%, var(--panel-top) 100%);
  }
  .card__wordmark {
    position: absolute;
    left: 0; top: 0;
    width: 742px;
    height: 598px;
    display: flex;
    align-items: center;
    justify-content: center;
    font-weight: 200;
    font-size: 64px;
    letter-spacing: 1px;
    line-height: 1;
  }
  .card__details {
    position: absolute;
    left: 0; top: 598px;
    width: 742px;
    height: 602px;
    background: var(--panel-bottom);
    text-align: center;
  }
  .card__name {
    position: absolute;
    left: 0; right: 0;
    top: 56px;
    font-weight: 200;
    font-size: 84px;
    line-height: 1;
    letter-spacing: 0.5px;
  }
  .card__contact {
    position: absolute;
    left: 0; right: 0;
    top: 300px;
    list-style: none;
    font-weight: 200;
    font-size: 56px;
    line-height: 80px;
  }
</style>
</head>
<body>
  <main class="card">
    <div class="card__brand-panel" role="img" aria-label="Dark grey backdrop with a faint repeating monogram pattern"></div>
    <div class="card__wordmark">corwin haldley</div>
    <section class="card__details">
      <h1 class="card__name">corwin haldley</h1>
      <ul class="card__contact">
        <li class="card__phone">0418592036</li>
        <li class="card__email">corwin@corwinhaldley-example.com</li>
        <li class="card__web">quietgoldenhourstudio.example.au</li>
      </ul>
    </section>
  </main>
</body>
</html>
```